Business Cards for IT Consulting Company (Managed Service Provider)

I am looking to have some business cards printed and would like some designs. We are an IT Consulting company based in Vancouver BC. I would like a nice clean and modern look to the cards. I have uploaded all the versions of my logo so parts can be used as needed. Here is a snippit from our website homepage:

Quillbrook Networks Ltd. is an IT Solutions Partner located in Vancouver BC, Canada. We offer IT solutions and support to customers in the greater Vancouver Area. With expertise in Microsoft platforms, as well as Linux and Mac OSX and over 12 years experience in the IT industry, Quillbrook Networks is dedicated to offering our clients top quality service and products. We take pride in the solutions we offer our customers. The greatest compliment a client can give us is to recommend our services.

Quillbrook Networks Ltd. offers a wide range of IT services from onsite service to remote support and managed service solutions. This allows clients to choose the support path that best suits their company’s needs. Supporting many different sized companies from small to enterprise level over the past 12 years Quillbrook Networks has the experience and expertise needed to ensure things run smoothly. Allowing our clients to focus on doing business.

Revolutionizing the way IT services are delivered.

Quillbrook Networks is dedicated to providing our clients with IT solutions that work and grow with them for years to come. This philosophy helps save money in the long run instead of replacing equipment constantly. Far too often IT solutions are not well thought out and while possibly solving the problem at hand, require replacement due to growth or quality within a very short time frame. Quillbrook Networks takes pride in providing solutions that will last and be able to accommodate growth without the need for replacement.

Industry/Entity Type

Information Technology

Contact Information for Business Card

Quillbrook Networks Ltd.
(Employee Name)
Eml: (Employees Email Address)
Web: quillbrook.me
Ph: 604-555-0148

Font styles to use
Serif
Sans Serif

Requirements
Must have
• The Company logo and company colors.
Nice to have
• - Our tag line: "Revolutionizing IT Services" or "Revolutionizing the way IT services are delivered."
• - Also I really like the idea of nature and technology together blending which is sort of where my logo came from so integrating that somehow onto the business cards would be great.

```html
<!DOCTYPE html>
<html lang="en">
<head>
<meta charset="utf-8">
<title>Quillbrook Networks Ltd. – Business Cards</title>
<link rel="stylesheet" href="https://fonts.googleapis.com/css2?family=Open+Sans:ital,wght@0,400;0,600;0,700;1,400&family=Roboto:wght@400&display=swap">
<style>
  :root {
    --backdrop: #a8a6a7;
    --card: #f3f4f4;
    --brand-blue: #1d8ed6;
    --ink: #3f3f42;
    --muted: #4a4a4d;
  }
  * { box-sizing: border-box; margin: 0; padding: 0; }
  html, body { width: 1200px; height: 1200px; overflow: hidden; }
  body {
    background: var(--backdrop);
    position: relative;
    font-family: "Open Sans", Arial, sans-serif;
  }
  .card {
    position: absolute;
    left: 244px;
    width: 712px;
    height: 418px;
    background: var(--card);
  }
  .card--front { top: 118px; }
  .card--back { top: 643px; }

  .brand {
    position: absolute;
    left: 112px;
    display: flex;
    align-items: center;
    gap: 26px;
  }
  .card--front .brand { top: 138px; }
  .card--back .brand { top: 58px; }
  .brand__dot {
    width: 64px; height: 64px;
    border-radius: 50%;
    background: var(--brand-blue);
    flex: none;
  }
  .brand__name {
    color: var(--brand-blue);
    font-weight: 600;
    line-height: 1;
  }
  .brand__word { display: block; font-size: 64px; letter-spacing: -0.5px; }
  .brand__suffix { display: block; font-size: 25px; letter-spacing: 1px; margin-top: 6px; }

  .tagline {
    position: absolute;
    left: 0; right: 0;
    bottom: 20px;
    display: flex;
    justify-content: center;
    align-items: center;
    gap: 18px;
    font-family: "Roboto", Arial, sans-serif;
    font-size: 19px;
    color: var(--muted);
    letter-spacing: 0.3px;
  }
  .tagline__rule {
    width: 108px;
    height: 3px;
    background: linear-gradient(90deg, transparent, var(--brand-blue) 25%, var(--brand-blue) 75%, transparent);
  }

  .person {
    position: absolute;
    left: 139px;
    top: 240px;
    width: 160px;
    text-align: right;
  }
  .person__name { font-size: 24px; font-weight: 600; color: var(--brand-blue); line-height: 1.2; }
  .person__role { font-size: 16px; font-style: italic; color: var(--muted); margin-top: 4px; }

  .contact {
    position: absolute;
    left: 325px;
    top: 228px;
    list-style: none;
    font-family: "Roboto", Arial, sans-serif;
    font-size: 18px;
    color: var(--ink);
  }
  .contact__item { display: flex; align-items: center; gap: 14px; height: 27px; }
  .contact__icon { width: 17px; height: 17px; fill: var(--brand-blue); flex: none; }
</style>
</head>
<body>
  <section class="card card--front" aria-label="Business card front">
    <div class="brand">
      <span class="brand__dot"></span>
      <span class="brand__name">
        <span class="brand__word">quillbrook</span>
        <span class="brand__suffix">NETWORKS LTD.</span>
      </span>
    </div>
    <p class="tagline"><span class="tagline__rule"></span>Revolutionizing IT Services<span class="tagline__rule"></span></p>
  </section>

  <section class="card card--back" aria-label="Business card back">
    <div class="brand">
      <span class="brand__dot"></span>
      <span class="brand__name">
        <span class="brand__word">quillbrook</span>
        <span class="brand__suffix">NETWORKS LTD.</span>
      </span>
    </div>

    <div class="person">
      <p class="person__name">Daniel Hart</p>
      <p class="person__role">Managing Director</p>
    </div>

    <ul class="contact">
      <li class="contact__item">
        <svg class="contact__icon" viewBox="0 0 20 20" aria-hidden="true"><path d="M2 6c0-2 3-4 8-4s8 2 8 4v2h-4V6H6v2H2z"/><path d="M5 9h10l2 8H3z"/><circle cx="10" cy="13" r="2" fill="#f3f4f4"/></svg>
        <span>604-555-0148</span>
      </li>
      <li class="contact__item">
        <svg class="contact__icon" viewBox="0 0 20 20" aria-hidden="true"><circle cx="10" cy="10" r="8"/><path d="M2 10h16M10 2c-3 3-3 13 0 16M10 2c3 3 3 13 0 16M4 5.5h12M4 14.5h12" stroke="#f3f4f4" stroke-width="1.2" fill="none"/></svg>
        <span>www.quillbrook.me</span>
      </li>
      <li class="contact__item">
        <svg class="contact__icon" viewBox="0 0 20 20" aria-hidden="true"><rect x="1" y="4" width="18" height="12"/><path d="M1 4l9 7 9-7" stroke="#f3f4f4" stroke-width="1.4" fill="none"/></svg>
        <span>support@quillbrook.me</span>
      </li>
    </ul>

    <p class="tagline"><span class="tagline__rule"></span>Revolutionizing IT Services<span class="tagline__rule"></span></p>
  </section>
</body>
</html>
```